A new presentation to our clients

we are a Real Estate agency, our website is www.lumibrasa.com and it’s time to have a new, fashion and remarcable Business Card. we want to differentiate ourselves from other companies so we want a business card that differentiates us. we want the business card to impact our customers. in the competitive market that we have today, we have to be different and it is this difference that we seek

Target Market(s)

Real Estate Clients

Contact Information for Business Card

We search a totaly diferent card from the usual

Font styles to use
Sans Serif

Colors
e34197

Requirements
Must have
• Logo, adress, phone contact, e-mail, photo, and our website
Nice to have
• We would like to see a modern business card
Should not have
• Houses or building draws

```html
<!DOCTYPE html>
<html lang="pt">
<head>
<meta charset="utf-8">
<title>Lumi Brasa – Business Card</title>
<link rel="stylesheet" href="https://fonts.googleapis.com/css2?family=Nunito:wght@500;600;700;800&display=swap">
<style>
  :root {
    --brand-pink: #e3206f;
    --text-dark: #3a3a3a;
    --text-grey: #8a8a8a;
    --card-white: #ffffff;
    --backdrop: #2a2a2a;
  }
  * { margin: 0; padding: 0; box-sizing: border-box; }
  html, body {
    width: 1200px;
    height: 791px;
    overflow: hidden;
    background: var(--backdrop);
    font-family: "Nunito", sans-serif;
  }
  .business-card {
    position: absolute;
    left: 80px;
    top: 100px;
    width: 1040px;
    height: 592px;
    background: var(--card-white);
    border-radius: 26px;
    overflow: hidden;
  }
  .brand-name {
    position: absolute;
    right: 49px;
    top: 52px;
    font-size: 80px;
    font-weight: 700;
    color: var(--brand-pink);
    letter-spacing: 1px;
    line-height: 1;
  }
  .person {
    position: absolute;
    left: 48px;
    top: 358px;
  }
  .person-name {
    font-size: 35px;
    font-weight: 800;
    color: var(--brand-pink);
    line-height: 1;
    letter-spacing: 0.5px;
  }
  .person-role {
    margin-top: 8px;
    font-size: 25px;
    font-weight: 700;
    color: var(--text-grey);
    line-height: 1;
    letter-spacing: 0.5px;
  }
  .divider {
    position: absolute;
    left: 48px;
    top: 449px;
    width: 943px;
    height: 3px;
    background: var(--brand-pink);
  }
  .contact-col {
    position: absolute;
    top: 470px;
    font-size: 23px;
    font-weight: 500;
    color: var(--text-dark);
    line-height: 31px;
  }
  .address { left: 48px; }
  .phones { left: 423px; }
  .online { left: 706px; }
  .contact-line {
    display: flex;
    align-items: center;
    gap: 10px;
    white-space: nowrap;
  }
  .contact-line svg {
    width: 22px;
    height: 22px;
    flex: none;
    fill: var(--brand-pink);
  }
  .bottom-band {
    position: absolute;
    left: 0;
    bottom: 0;
    width: 100%;
    height: 20px;
    background: var(--brand-pink);
  }
</style>
</head>
<body>
  <main class="business-card">
    <div class="brand-name">Lumi Brasa</div>

    <div class="person">
      <div class="person-name">RUI MATOS</div>
      <div class="person-role">CEO/FOUNDER</div>
    </div>

    <div class="divider"></div>

    <address class="contact-col address" style="font-style:normal">
      <div class="contact-line">Rua das Flores Altas, 118</div>
      <div class="contact-line">4410-233, Vila Nova de Gaia</div>
    </address>

    <div class="contact-col phones">
      <div class="contact-line">
        <svg viewBox="0 0 24 24" aria-hidden="true"><path d="M6.6 10.8a15.1 15.1 0 0 0 6.6 6.6l2.2-2.2c.3-.3.7-.4 1-.2 1.1.4 2.3.6 3.6.6.6 0 1 .4 1 1V20c0 .6-.4 1-1 1A17 17 0 0 1 3 4c0-.6.4-1 1-1h3.5c.6 0 1 .4 1 1 0 1.3.2 2.5.6 3.6.1.3 0 .7-.2 1z"/></svg>
        <span>(+351) 220 418 560</span>
      </div>
      <div class="contact-line">
        <svg viewBox="0 0 24 24" aria-hidden="true"><path d="M6 2h12v6H6z M3 9h18a1 1 0 0 1 1 1v8h-4v4H6v-4H2v-8a1 1 0 0 1 1-1z M8 15v5h8v-5z"/></svg>
        <span>(+351) 220 418 561</span>
      </div>
    </div>

    <div class="contact-col online">
      <div class="contact-line">
        <svg viewBox="0 0 24 24" aria-hidden="true"><path d="M2 5h20v14H2z" fill="none"/><path d="M2 5h20v14H2V5zm2 2v.5l8 5 8-5V7l-8 5z"/></svg>
        <span>geral@lumibrasa.com</span>
      </div>
      <div class="contact-line">
        <svg viewBox="0 0 24 24" aria-hidden="true"><circle cx="12" cy="12" r="10"/><path d="M12 2a10 10 0 0 1 0 20M2 12h20M12 2c-3 3-3 17 0 20" stroke="#fff" stroke-width="1.5" fill="none"/></svg>
        <span>www.lumibrasa.com</span>
      </div>
    </div>

    <div class="bottom-band"></div>
  </main>
</body>
</html>
```